Sales sheet for printing and embroidery apparel items - Copper Hollow Graphics

I would like a one page flyer or sales sheet that I would use as a template to send different images of apparel we produce. I have attached examples of layouts I like.
- Ideally, it would have space for 3-5 items.
- I would like it one page only - not a folding flyer.
- Our companies name is Copper Hollow Graphics.
- This will be used for many different products and markets so I don't need wording/copy. You can use wording from the 7M9 or T58 flyer.

Colors
0054AA
0677BA
7BADD7
CADEEF
E8F1F8
00AB8E
00BBA5
67D7C9
C6EFE9
E9F9F6
FFC000
F8CF3A
FAE287
FDF2CF
FEFAEE

Requirements
Must have
• Places for between 3 and 5 images of apparel (t-shirts, hats etc)

```html
<!DOCTYPE html>
<html lang="en">
<head>
<meta charset="utf-8">
<title>Copper Hollow Graphics – Sales Sheet</title>
<link href="https://fonts.googleapis.com/css2?family=Teko:wght@600;700&family=Roboto:wght@400;500;700&family=Rubik:ital,wght@1,800&display=swap" rel="stylesheet">
<style>
:root{
  --blue:#0054AA;
  --blue-mid:#0677BA;
  --blue-soft:#7BADD7;
  --blue-pale:#CADEEF;
  --blue-mist:#E8F1F8;
  --teal:#00AB8E;
  --teal-mid:#00BBA5;
  --teal-pale:#C6EFE9;
  --yellow:#FFC000;
  --yellow-soft:#F8CF3A;
  --ink:#1c1c1c;
  --white:#ffffff;
  --rule-light:rgba(255,255,255,.4);
}
*{box-sizing:border-box;margin:0;padding:0}
html,body{width:906px;height:1200px;overflow:hidden;background:var(--white)}
body{position:relative;font-family:"Roboto",Arial,sans-serif;color:var(--ink)}
.abs{position:absolute}

/* Header */
.hero-band{left:305px;top:26px;width:601px;height:211px;background:var(--blue)}
.hero-photo{left:0;top:0;width:360px;height:264px}
.brand-card{left:213px;top:56px;width:74px;height:92px;background:var(--white);display:flex;flex-direction:column;align-items:center;justify-content:center;gap:6px;padding:6px}
.brand-card .mark{width:34px;height:34px;background:var(--blue)}
.brand-card .name{font-family:"Teko",sans-serif;font-weight:600;font-size:14px;line-height:.9;color:var(--blue);text-align:center;text-transform:uppercase}
.headline{left:426px;top:44px;width:470px;font-family:"Teko",sans-serif;font-weight:700;color:var(--white);text-transform:uppercase;letter-spacing:.5px}
.headline span{display:block;white-space:nowrap}
.headline .big{font-size:75px;line-height:56px}
.headline .small{font-size:58px;line-height:58px;margin-top:4px}

/* Benefits */
.benefits{left:0;top:282px;width:906px;display:flex;justify-content:space-around;padding:0 12px}
.benefit{width:190px;text-align:center}
.benefit svg{width:72px;height:66px;display:block;margin:0 auto}
.benefit h3{font-family:"Teko",sans-serif;font-weight:600;font-size:22px;color:var(--blue);margin-top:12px;line-height:1;letter-spacing:.3px}
.benefit p{font-size:12.5px;line-height:1.3;margin-top:5px;color:var(--ink)}

/* Products */
.section-title{font-family:"Teko",sans-serif;font-weight:700;font-size:30px;line-height:1;text-align:center;left:0;width:906px}
.products-title{top:432px;color:var(--teal)}
.rule{height:2px;width:58px;left:424px;background:var(--yellow)}
.products-rule{top:469px}
.product-grid{left:26px;top:487px;display:flex;gap:10px}
.product-slot{width:162px;height:151px;background:var(--blue-mist);border-radius:2px}

/* Offer band */
.offer-band{left:0;top:667px;width:906px;height:179px;background:var(--blue)}
.offer-title{top:704px;color:var(--white)}
.offer-rule{top:740px}
.offers{left:0;top:760px;width:906px;height:70px;display:flex;align-items:center}
.offer{display:flex;align-items:center;gap:8px;color:var(--white);font-weight:700;font-size:14px;line-height:1.25;padding-left:18px;height:100%;border-right:1px solid var(--rule-light)}
.offer:last-child{border-right:none}
.offer svg{flex:none}
.offer-1{width:177px}
.offer-2{width:195px;padding-left:10px}
.offer-3{width:252px;padding-left:18px}
.offer-4{width:282px;padding-left:16px}

/* Steps band */
.steps-band{left:0;top:846px;width:906px;height:258px;background:var(--teal)}
.steps-title{left:0;width:906px;top:872px;text-align:center;font-family:"Rubik",sans-serif;font-style:italic;font-weight:800;font-size:29px;color:var(--white);letter-spacing:.5px}
.steps-rule{top:919px}
.step{top:946px;width:244px;text-align:center;color:var(--white)}
.step svg{display:block;margin:0 auto}
.step h4{font-family:"Rubik",sans-serif;font-style:italic;font-weight:800;font-size:16.5px;margin-top:6px;letter-spacing:.3px}
.step p{font-size:12.5px;line-height:1.35;margin-top:3px}
.step-arrow{top:1006px}

/* Footer */
.footer-title{left:24px;top:1120px;font-family:"Teko",sans-serif;font-weight:700;font-size:32px;color:var(--blue);line-height:1;letter-spacing:.3px}
.contact{top:1155px;display:flex;align-items:center;gap:10px}
.contact .phone{font-family:"Teko",sans-serif;font-weight:700;font-size:28px;color:var(--ink);line-height:1}
.contact .email{font-size:15px;color:var(--ink)}
.icon-dot{width:26px;height:26px;border-radius:50%;background:var(--teal);display:flex;align-items:center;justify-content:center}
.badges{left:488px;top:1124px;width:388px;display:flex;align-items:center;justify-content:space-between}
.badge{background:var(--blue-pale)}
.badge.round{width:26px;height:26px;border-radius:50%}
.badge.wide{width:56px;height:24px;border-radius:2px}
.socials{left:814px;top:1166px;display:flex;gap:6px}
.social{width:18px;height:18px;border-radius:50%;background:var(--blue)}
</style>
</head>
<body>

<!-- Header -->
<div class="abs hero-band"></div>
<svg class="abs hero-photo" viewBox="0 0 360 264" role="img" aria-label="Photo of a trade show booth with a rack of shirts and a branded banner">
  <defs>
    <clipPath id="hero-clip">
      <rect x="0" y="0" width="180" height="264"/>
      <ellipse cx="180" cy="132" rx="179" ry="132"/>
    </clipPath>
    <linearGradient id="hero-tone" x1="0" y1="0" x2="1" y2="1">
      <stop offset="0" stop-color="#6b6470"/>
      <stop offset=".45" stop-color="#8a8f98"/>
      <stop offset=".75" stop-color="#d9773a"/>
      <stop offset="1" stop-color="#4f6b86"/>
    </linearGradient>
  </defs>
  <rect width="360" height="264" fill="url(#hero-tone)" clip-path="url(#hero-clip)"/>
</svg>
<div class="abs brand-card">
  <div class="mark"></div>
  <div class="name">Copper Hollow Graphics</div>
</div>
<h1 class="abs headline">
  <span class="big">Order shirts</span>
  <span class="big">for your all</span>
  <span class="small">of your retreats</span>
</h1>

<!-- Benefits -->
<section class="abs benefits">
  <div class="benefit">
    <svg viewBox="0 0 70 64" fill="none" stroke="#00AB8E" stroke-width="1.6">
      <path d="M14 22l18-16 24 14-18 16z"/>
      <path d="M14 22v26l24 14V36"/><path d="M38 62l18-16V20"/>
      <path d="M14 28l24 14 18-16M14 34l24 14 18-16M14 40l24 14 18-16"/>
    </svg>
    <h3>LOW MINIMUMS</h3>
    <p>Order as few as 24 pieces<br>to get started.</p>
  </div>
  <div class="benefit">
    <svg viewBox="0 0 70 64" fill="none" stroke="#00AB8E" stroke-width="1.6">
      <path d="M12 8l6-3 22 42 22-10"/><circle cx="42" cy="52" r="5"/>
      <rect x="30" y="16" width="16" height="16" transform="rotate(-25 38 24)"/>
      <rect x="38" y="30" width="16" height="14" transform="rotate(-25 46 37)"/>
      <path d="M6 34h12M4 40h14M8 46h12"/>
    </svg>
    <h3>FAST TURNAROUND</h3>
    <p>2-week standard delivery.</p>
  </div>
  <div class="benefit">
    <svg viewBox="0 0 70 64" fill="none" stroke="#00AB8E" stroke-width="1.6">
      <circle cx="35" cy="10" r="7"/><path d="M24 60V28q0-8 11-8t11 8v32"/>
      <circle cx="20" cy="14" r="5"/><circle cx="50" cy="14" r="5"/>
      <path d="M14 52V30q0-8 8-8M56 52V30q0-8-8-8"/>
      <circle cx="8" cy="18" r="4"/><circle cx="62" cy="18" r="4"/>
      <path d="M4 46V30q0-6 6-6M66 46V30q0-6-6-6"/>
    </svg>
    <h3>REAL PEOPLE</h3>
    <p>Work with our team of<br>experts and artists.</p>
  </div>
  <div class="benefit">
    <svg viewBox="0 0 70 64" fill="none" stroke="#00AB8E" stroke-width="1.6">
      <path d="M35 6l16 6v12q0 14-16 20Q19 38 19 24V12z"/>
      <circle cx="35" cy="24" r="8"/><path d="M31 24l3 3 5-6"/>
      <path d="M6 44l12 8h20l14-6q6-2 4 2l-16 12H18L6 54"/>
      <path d="M10 10l4 4M60 10l-4 4M6 24h6M58 24h6"/>
    </svg>
    <h3>GUARANTEED</h3>
    <p>We promise accurate,<br>quality work.</p>
  </div>
</section>

<!-- Products -->
<h2 class="abs section-title products-title">OUR PRODUCTS</h2>
<div class="abs rule products-rule"></div>
<div class="abs product-grid">
  <div class="product-slot" role="img" aria-label="Apparel product image 1"></div>
  <div class="product-slot" role="img" aria-label="Apparel product image 2"></div>
  <div class="product-slot" role="img" aria-label="Apparel product image 3"></div>
  <div class="product-slot" role="img" aria-label="Apparel product image 4"></div>
  <div class="product-slot" role="img" aria-label="Apparel product image 5"></div>
</div>

<!-- Offer -->
<div class="abs offer-band"></div>
<h2 class="abs section-title offer-title">WE OFFER</h2>
<div class="abs rule offer-rule"></div>
<div class="abs offers">
  <div class="offer offer-1">
    <svg width="40" height="40" viewBox="0 0 36 36" fill="#fff">
      <circle cx="18" cy="20" r="11" fill="none" stroke="#fff" stroke-width="5" stroke-dasharray="5 3"/>
      <rect x="15" y="2" width="6" height="18"/>
    </svg>
    <span>Art Design</span>
  </div>
  <div class="offer offer-2">
    <svg width="44" height="30" viewBox="0 0 38 26" fill="#fff">
      <rect x="0" y="2" width="24" height="16" rx="2"/>
      <path d="M25 7h7l5 6v5H25z"/>
      <circle cx="8" cy="21" r="3.5"/><circle cx="30" cy="21" r="3.5"/>
    </svg>
    <span>Free Shipping</span>
  </div>
  <div class="offer offer-3">
    <svg width="36" height="36" viewBox="0 0 30 30" fill="#fff">
      <circle cx="18" cy="10" r="9"/>
      <text x="18" y="14" text-anchor="middle" font-family="Roboto,sans-serif" font-weight="700" font-size="11" fill="#0054AA">$</text>
      <rect x="0" y="18" width="5" height="11"/>
      <path d="M7 20h8l6 2h7v4l-9 3H7z"/>
    </svg>
    <span>We Pay ALL Royalties<br>to the Movement</span>
  </div>
  <div class="offer offer-4">
    <svg width="38" height="36" viewBox="0 0 32 30" fill="#fff">
      <path d="M10 1l6 3 6-3 10 7-4 6-4-2v17H8V12l-4 2-4-6z"/>
    </svg>
    <span>Many Options of Shirt<br>Styles and Colors</span>
  </div>
</div>

<!-- Steps -->
<div class="abs steps-band"></div>
<h2 class="abs steps-title">HOW TO START AN ORDER</h2>
<div class="abs rule steps-rule"></div>

<div class="abs step" style="left:128px;transform:translateX(-50%);left:250px"></div>

<div class="abs step" style="left:24px">
  <svg width="38" height="38" viewBox="0 0 34 32" fill="none" stroke="#fff" stroke-width="1.8">
    <circle cx="14" cy="14" r="12"/><path d="M23 23l8 8"/>
    <path d="M7 17h14v-3l-3-4h-8l-3 4z"/>
  </svg>
  <h4>CHOOSE YOUR RIDE</h4>
  <p>Send us a picture, or let us know the make and model of the vehicle you would like featured on your apparel.</p>
</div>
<svg class="abs step-arrow" style="left:283px" width="34" height="8" viewBox="0 0 34 8" fill="none" stroke="#fff" stroke-width="1.3"><path d="M0 4h32M28 1l4 3-4 3"/></svg>

<div class="abs step" style="left:331px">
  <svg width="38" height="38" viewBox="0 0 34 32" fill="none" stroke="#fff" stroke-width="1.8">
    <path d="M11 2l6 3 6-3 9 6-4 6-4-2v18H10V12l-4 2-4-6z"/>
    <path d="M17 14v12M17 20h5v6"/>
  </svg>
  <h4>PICK YOUR GEAR</h4>
  <p>We will help you choose your t-shirts, sweatshirts or other apparel items and determine sizes and quantities.</p>
</div>
<svg class="abs step-arrow" style="left:601px" width="34" height="8" viewBox="0 0 34 8" fill="none" stroke="#fff" stroke-width="1.3"><path d="M0 4h32M28 1l4 3-4 3"/></svg>

<div class="abs step" style="left:640px">
  <svg width="38" height="38" viewBox="0 0 34 32" fill="none" stroke="#fff" stroke-width="1.8">
    <path d="M4 28L28 4l3 3L7 31z"/>
    <path d="M4 4l24 24M8 2a5 5 0 00-6 6M26 30a5 5 0 006-6"/>
  </svg>
  <h4>WE CUSTOMIZE</h4>
  <p>We make the magic happen and our team of expert artists will design your shirts and get a proof out to you. Upon order</p>
</div>

<!-- Footer -->
<h2 class="abs footer-title">WE’D LOVE TO WORK WITH YOU!</h2>
<div class="abs contact" style="left:16px">
  <div class="icon-dot">
    <svg width="14" height="14" viewBox="0 0 14 14" fill="#fff"><path d="M3 1l2 3-1.5 1.5q1.5 3 5 5L10 9l3 2-1.5 2.5Q6 13 1 3z"/></svg>
  </div>
  <span class="phone">555-018-2746</span>
</div>
<div class="abs contact" style="left:292px">
  <div class="icon-dot">
    <svg width="14" height="14" viewBox="0 0 14 14" fill="#fff"><path d="M3 1l2 3-1.5 1.5q1.5 3 5 5L10 9l3 2-1.5 2.5Q6 13 1 3z"/></svg>
  </div>
  <span class="email">riley@copperhollowtees.com</span>
</div>

<div class="abs badges" aria-label="Partner and certification badges">
  <div class="badge round"></div>
  <div class="badge round"></div>
  <div class="badge wide"></div>
  <div class="badge wide" style="width:36px"></div>
  <div class="badge round"></div>
  <div class="badge wide" style="width:26px"></div>
</div>
<div class="abs socials" aria-label="Social media links">
  <div class="social"></div>
  <div class="social"></div>
  <div class="social"></div>
</div>

</body>
</html>
```